Business Card for premium dental clinic

We are a premium dental clinic based in Brasov, Romania with more than 15 year on the market, providing quality dental treatment made by a team of more specialized dentists, working with modern equipment as a solution to beautiful and healthy teeth.

Our current logo for the clinic use 2 square with colors black and gold - dr Ternisu - studio, using family fonts Bodoni, Myriad Pro and Segoe Print.
Depending on the printing we used some gold CMYK background or gold foil picture background or a gold gradient.
We want a business card:
- eye catching business card
- distinguished business card
- premium design
- to keep the color scheme of black and gold
- to attract the customers to spent time reading the information
- modern concept

```html
<!DOCTYPE html>
<html lang="en">
<head>
<meta charset="utf-8">
<title>dr Ternisu studio – Business Card</title>
<link rel="stylesheet" href="https://fonts.googleapis.com/css2?family=Lato:wght@400;700;900&display=swap">
<style>
  :root {
    --gold: #b98a2c;
    --black: #050505;
    --paper: #fbf6f6;
    --ink: #1c1c1c;
    --rule: #9a9a9a;
    --stage: #e4e2df;
  }
  * { box-sizing: border-box; margin: 0; padding: 0; }
  html, body { width: 1200px; height: 782px; overflow: hidden; }
  body {
    background: var(--stage);
    font-family: "Lato", Arial, sans-serif;
    position: relative;
  }
  .card {
    position: absolute;
    top: 236px;
    width: 540px;
    height: 310px;
    overflow: hidden;
    box-shadow: 0 6px 18px rgba(0,0,0,.18);
  }

  /* Front */
  .card--front { left: 40px; background: var(--black); }
  .front-brand {
    position: absolute;
    left: 0; right: 0; top: 50%;
    transform: translateY(-50%);
    display: flex;
    align-items: center;
    justify-content: center;
    gap: 18px;
  }
  .front-brand__square { width: 34px; height: 34px; background: var(--gold); }
  .front-brand__name {
    color: var(--paper);
    font-size: 40px;
    font-weight: 400;
    letter-spacing: .5px;
  }
  .front-band {
    position: absolute;
    left: 0; right: 0; bottom: 0;
    height: 26px;
    background: var(--gold);
  }

  /* Back */
  .card--back { left: 620px; background: var(--paper); }
  .back-brand {
    position: absolute;
    left: 28px; top: 100px;
    width: 230px;
    display: flex;
    align-items: center;
    gap: 12px;
  }
  .back-brand__square { width: 22px; height: 22px; background: var(--gold); flex: none; }
  .back-brand__name { color: var(--black); font-size: 23px; font-weight: 400; }
  .divider {
    position: absolute;
    left: 282px; top: 62px;
    width: 1px; height: 160px;
    background: var(--rule);
  }
  .contact {
    position: absolute;
    left: 302px; top: 66px;
    color: var(--ink);
    font-size: 14.5px;
    line-height: 1.35;
  }
  .contact__name {
    color: var(--gold);
    font-weight: 900;
    font-size: 17px;
    letter-spacing: .6px;
    text-transform: uppercase;
  }
  .contact__role { margin-bottom: 4px; }
  .contact__line { display: flex; align-items: center; gap: 6px; }
  .contact__line svg { width: 12px; height: 12px; fill: var(--gold); flex: none; }
  .contact__address { margin-top: 3px; }
  .back-strip {
    position: absolute;
    left: 0; bottom: 0;
    width: 300px; height: 12px;
    background: var(--black);
  }
  .back-band {
    position: absolute;
    right: 0; bottom: 0;
    width: 270px; height: 26px;
    background: var(--gold);
    clip-path: polygon(14px 0, 100% 0, 100% 100%, 0 100%);
  }
</style>
</head>
<body>

  <section class="card card--front" aria-label="Business card front">
    <div class="front-brand">
      <span class="front-brand__square"></span>
      <span class="front-brand__name">dr Ternisu studio</span>
    </div>
    <div class="front-band"></div>
  </section>

  <section class="card card--back" aria-label="Business card back">
    <div class="back-brand">
      <span class="back-brand__square"></span>
      <span class="back-brand__name">dr Ternisu studio</span>
    </div>

    <div class="divider"></div>

    <div class="contact">
      <p class="contact__name">Andrei Mirescu</p>
      <p class="contact__role">Managing Director</p>
      <p class="contact__line">
        <svg viewBox="0 0 24 24" aria-hidden="true"><path d="M6.6 10.8a15 15 0 0 0 6.6 6.6l2.2-2.2a1 1 0 0 1 1-.25 11.4 11.4 0 0 0 3.6.57 1 1 0 0 1 1 1V20a1 1 0 0 1-1 1A17 17 0 0 1 3 4a1 1 0 0 1 1-1h3.5a1 1 0 0 1 1 1c0 1.25.2 2.45.57 3.57a1 1 0 0 1-.25 1z"/></svg>
        044-123 456 789
      </p>
      <p class="contact__line">
        <svg viewBox="0 0 24 24" aria-hidden="true"><path d="M2 5h20v14H2z M2 5l10 8 10-8" /></svg>
        info@webname.com
      </p>
      <p class="contact__line">
        <svg viewBox="0 0 24 24" aria-hidden="true"><circle cx="12" cy="12" r="10"/></svg>
        www.websitename.com
      </p>
      <p class="contact__address">421, Address line here<br>Country Name, 45452</p>
    </div>

    <div class="back-strip"></div>
    <div class="back-band"></div>
  </section>

</body>
</html>
```